Hardcore nerd needs to stand out in a sea of dull Defence business cards

Wombarra Devices is a new Australian consulting engineering company that turns research and theory into practical systems. No evangelistic fluff, just mathematics and physics into electronic and optical circuits for consumer products, scientific research or Defence applications.

We already have a recognised logo (provided) which is often dark blue/black on a light background but we're open to other combinations. (Us engineers tend to have limited aesthetic imagination :)

Some of our recent products have included:
* Instrumentation for electrical testing,
* Radar jammers,
* GPS antenna design,
* Satellite tracking systems,
* High power lasers

We're open to both single and double-sided designs - happy to be convinced either way.

P.S. Another group is working on the web page, so - alas - our web site is currently of no use for images/ideas...

Target Market(s)

Engineering managers,
Scientists

Contact Information for Business Card

Dr Colin Harte
R&D Engineer

colin@wombarradevices.com.au
0427 563 710

PO Box XXX (to be confirmed)
Kelsby ACT 2917
Australia

Font styles to use
Serif
Sans Serif

Colors

Designer to choose colors to be used in the design.

Requirements
Must have
• My contact details!
• I've had many (great) "bold and plain" designs submitted already, so feel free to be artistically creative :)
• Happy to take advice re fonts/colours/printability etc.
Nice to have
• I'm not sure if "lists" are more at home on a CV than a business card, but representative services include:
• Applied electromagnetics
• RF and high speed electronics
• Signal and image processing
• Electro-optical and laser systems
• Concept-to-prototype design services
• If you're considering double sided cards, then often measuring/alignment grids/rulers feature on the back of similar cards.
• e.g. https://www.veltranoptics.example/newgrouppage9.cfm?objectgroup_id=4183
• https://www.veltranoptics.example/newgrouppage9.cfm?objectgroup_ID=4185
• ..or even a "Smith chart" (google will return lots)
• Generic images to represent a capability might work - googling images associated with keyword for each of these areas might help:
• - "passive radar", "phased array", "fdtd", "vircator"
• RF and high speed electronic design
• - "smith chart", "microstrip circuits", "dimensioned drawing", "electronic schematic"
• - "dft", "iir filter"
• - "optical cavity". "laser energy level diagram"
• Background/watermarked images outlines/wireframes/schematics would probably look OK.
Should not have
• If a list of projects/services is provided, it is important not to make the client feel that this is "all" the company can do. Engineering design is a creative discipline (like graphics :)
• Please, no stock "military" snaps like planes, missiles, etc!

```html
<!DOCTYPE html>
<html lang="en">
<head>
<meta charset="utf-8">
<title>Wombarra Devices – Business Card</title>
<link href="https://fonts.googleapis.com/css2?family=Lato:wght@400;700;900&display=swap" rel="stylesheet">
<style>
  :root {
    --navy: #1e2a5e;
    --orange: #f08019;
    --white: #ffffff;
    --stage: #e9e7e3;
    --ink: #2b2f3a;
  }
  * { box-sizing: border-box; margin: 0; padding: 0; }
  html, body {
    width: 1200px; height: 900px; overflow: hidden;
    background: var(--stage);
    font-family: "Lato", Arial, sans-serif;
  }
  .sheet {
    position: relative; width: 1200px; height: 900px;
    display: flex; justify-content: center; align-items: center; gap: 120px;
  }
  .card {
    position: relative; width: 340px; height: 595px;
    border-radius: 22px; overflow: hidden;
    box-shadow: 0 10px 28px rgba(0,0,0,0.18);
  }

  /* Front */
  .card-front { background: var(--navy); }
  .front-brand {
    position: absolute; left: 50%; top: 50%;
    width: 520px;
    transform: translate(-50%, -50%) rotate(90deg);
    display: flex; align-items: center; justify-content: center; gap: 26px;
    color: var(--white);
  }
  .brand-dot {
    width: 110px; height: 110px; border-radius: 50%;
    background: var(--white); flex: none;
  }
  .front-brand .brand-name {
    font-weight: 900; font-size: 44px; line-height: 1.05;
    letter-spacing: 2px; text-transform: uppercase;
  }

  /* Back */
  .card-back { background: var(--white); }
  .back-brand {
    position: absolute; top: 70px; left: 0; right: 0;
    display: flex; align-items: center; justify-content: center; gap: 14px;
  }
  .back-brand .brand-dot {
    width: 58px; height: 58px; background: var(--navy);
  }
  .back-brand .brand-name {
    color: var(--orange); font-weight: 900; font-size: 22px; line-height: 1.1;
    letter-spacing: 1px; text-transform: uppercase;
  }
  .person {
    position: absolute; top: 228px; left: 0; right: 0; text-align: center;
  }
  .person-name { color: var(--navy); font-weight: 700; font-size: 27px; }
  .person-role { color: var(--orange); font-size: 18px; margin-top: 2px; }

  .contact {
    position: absolute; top: 335px; left: 0; right: 0; text-align: center;
    color: var(--ink);
  }
  .contact-icons { display: flex; justify-content: center; gap: 8px; }
  .contact-rule {
    width: 110px; height: 1px; margin: 6px auto 8px;
    background: linear-gradient(90deg, transparent, var(--navy), transparent);
  }
  .contact-line { font-size: 17px; line-height: 1.45; }
  .contact-line.email { font-size: 14.5px; }

  .address-band {
    position: absolute; left: 0; right: 0; bottom: 0; height: 138px;
    background: var(--navy); color: var(--white);
    display: flex; flex-direction: column; justify-content: center; align-items: center;
    font-size: 17px; line-height: 1.4;
  }
</style>
</head>
<body>
<main class="sheet">
  <section class="card card-front" aria-label="Card front">
    <div class="front-brand">
      <span class="brand-dot"></span>
      <span class="brand-name">Wombarra<br>Devices</span>
    </div>
  </section>

  <section class="card card-back" aria-label="Card back">
    <div class="back-brand">
      <span class="brand-dot"></span>
      <span class="brand-name">Wombarra<br>Devices</span>
    </div>

    <div class="person">
      <p class="person-name">Dr Colin Harte</p>
      <p class="person-role">R&amp;D Engineer</p>
    </div>

    <div class="contact">
      <div class="contact-icons">
        <svg width="16" height="16" viewBox="0 0 24 24" aria-label="Phone">
          <path fill="#f08019" d="M6.6 10.8a15 15 0 0 0 6.6 6.6l2.2-2.2c.3-.3.7-.4 1-.2 1.1.4 2.3.6 3.6.6.6 0 1 .4 1 1V20c0 .6-.4 1-1 1A17 17 0 0 1 3 4c0-.6.4-1 1-1h3.5c.6 0 1 .4 1 1 0 1.3.2 2.5.6 3.6.1.3 0 .7-.2 1z"/>
        </svg>
        <svg width="18" height="16" viewBox="0 0 24 20" aria-label="Email">
          <rect x="2" y="6" width="20" height="13" rx="1.5" fill="none" stroke="#f08019" stroke-width="2"/>
          <path d="M2 7l10 7 10-7" fill="none" stroke="#f08019" stroke-width="2"/>
        </svg>
      </div>
      <div class="contact-rule"></div>
      <p class="contact-line">0427 563 710</p>
      <p class="contact-line email">colin@wombarradevices.com.au</p>
    </div>

    <div class="address-band">
      <p>PO Box XXX</p>
      <p>Kelsby ACT 2917, Australia</p>
    </div>
  </section>
</main>
</body>
</html>
```